Powerpoint, Graphics for Sermon Series

I am starting a sermon series on the short letters if Scripture that are between Hebrews and Revelation. The sermon series will be called "Walking Unmarked Trails: Lasting Lessons from Quiet Hills."

Think about finding a packet of letters in an Attic. There is only the dialogue of the writer. We don't know exactly what the receivers were going through or even what their response to the letters were/are!

Target Market(s)

Local Church

Industry/Entity Type

Christian

Font styles to use
Serif
Sans Serif

Colors

Designer to choose colors to be used in the design.

Requirements
Must have
• Powerpoint Slide with Title -
• Background Slide -
• It would be great to have both JPG, PNG, and Photoshop/Indesign that can be used for powerpoint, both in 4x3 ration and wide... Need Title Slide with typography and background slide for text to go over the top of.
• Stick with the theme -- Walking Unmarked Trails
• I am including our church logo, but don't feel like you need to use it in anyway.
Nice to have
• Social Media Slides - Square Slide, Facebook Header
• Greyscale Version?

```html
<!DOCTYPE html>
<html lang="en">
<head>
<meta charset="utf-8">
<title>Walking Unmarked Trails — Sermon Series Title Slide</title>
<link href="https://fonts.googleapis.com/css2?family=Roboto+Slab:wght@500;700&display=swap" rel="stylesheet">
<style>
  :root {
    --paper: #ffffff;
    --title-brown: #6b2e12;
    --arc-orange: #f39a1c;
    --photo-light: #f6c58c;
    --photo-mid: #d9823e;
    --photo-deep: #9c4a18;
  }
  html, body {
    margin: 0;
    padding: 0;
    overflow: hidden;
    background: var(--paper);
  }
  .slide {
    position: relative;
    width: 1200px;
    height: 900px;
    overflow: hidden;
    background: var(--paper);
    font-family: "Roboto Slab", Georgia, serif;
  }
  .slide__art {
    position: absolute;
    inset: 0;
  }
  .series-title {
    position: absolute;
    right: 27px;
    top: 368px;
    margin: 0;
    text-align: right;
    color: var(--title-brown);
    font-weight: 700;
    font-size: 36px;
    line-height: 56px;
    letter-spacing: 0.2px;
  }
  .series-title__line {
    display: block;
  }
  .title-rule {
    position: absolute;
    height: 2px;
    background: var(--title-brown);
  }
  .title-rule--long { left: 742px; width: 263px; top: 482px; }
  .title-rule--short { left: 800px; width: 150px; top: 492px; }
  .church-name {
    position: absolute;
    right: 30px;
    top: 735px;
    display: flex;
    align-items: center;
    gap: 16px;
    color: var(--title-brown);
    font-weight: 700;
    font-size: 40px;
  }
  .church-name__mark {
    width: 26px;
    height: 26px;
    background: var(--title-brown);
  }
</style>
</head>
<body>
  <main class="slide">
    <svg class="slide__art" width="1200" height="900" viewBox="0 0 1200 900" xmlns="http://www.w3.org/2000/svg">
      <defs>
        <linearGradient id="photoTone" x1="0.8" y1="0" x2="0.1" y2="1">
          <stop offset="0" stop-color="var(--photo-light)"/>
          <stop offset="0.45" stop-color="var(--photo-mid)"/>
          <stop offset="1" stop-color="var(--photo-deep)"/>
        </linearGradient>
      </defs>
      <path role="img" aria-label="Warm orange-toned photograph of a closed Bible with a cross on its cover resting in a church pew"
            d="M0 0 H660 Q345 450 690 900 H0 Z" fill="url(#photoTone)"/>
      <path d="M660 0 Q345 450 690 900" fill="none" stroke="var(--arc-orange)" stroke-width="18"/>
    </svg>

    <h1 class="series-title">
      <span class="series-title__line">Walking Unmarked Trails</span>
      <span class="series-title__line">Lasting Lessons from Quiet Hills</span>
    </h1>
    <div class="title-rule title-rule--long"></div>
    <div class="title-rule title-rule--short"></div>

    <div class="church-name">
      <span class="church-name__mark"></span>
      <span>Cedar Ridge Church</span>
    </div>
  </main>
</body>
</html>
```